Desing for real estate offers- Package system

The word should be graphically clear and understandable. There are 3 packages that the customer can buy: the basic package is red, the medicinal package is green and the carefree package is blue. See the Word document in the appendix. End file should be a Word, as we need to chance the text. It should also match the website as well as the business card.
https://brivotelo.domvanta.ch/
Colors:
Green 1: R: 187, G: 214, B: 49
Green 2: R: 119, G: 187, W: 66

Target Market(s)

Real estate company

Font styles to use
Serif
Sans Serif

```html
<!DOCTYPE html>
<html lang="de">
<head>
<meta charset="utf-8">
<title>Individuelle Vermarktungspakete – Brivotelo</title>
<link href="https://fonts.googleapis.com/css2?family=Bebas+Neue&family=Roboto:wght@400;500;700&display=swap" rel="stylesheet">
<style>
  :root {
    --green-1: #bbd631;
    --green-2: #77bb42;
    --red: #ec2024;
    --blue: #4686c6;
    --grey: #6d6e71;
    --white: #ffffff;
    --page: #ffffff;
  }
  * { box-sizing: border-box; margin: 0; padding: 0; }
  html, body {
    width: 1200px; height: 1200px; overflow: hidden;
    background: var(--page);
    font-family: "Roboto", Arial, sans-serif;
  }
  .flyer {
    position: absolute; left: 192px; top: 23px;
    width: 959px; height: 1357px;
    transform: scale(0.85); transform-origin: top left;
    background: var(--white);
    box-shadow: 0 0 6px rgba(0,0,0,0.18);
    overflow: hidden;
  }
  .top-band { position: absolute; left: 0; top: 0; width: 100%; height: 18px; display: flex; }
  .top-band span:first-child { width: 580px; background: var(--green-1); }
  .top-band span:last-child { flex: 1; background: var(--green-2); }

  .flyer-title {
    position: absolute; left: 18px; top: 46px;
    font-size: 59px; font-weight: 700; color: var(--green-2);
    white-space: nowrap; letter-spacing: 0.2px;
  }
  .flyer-note {
    position: absolute; left: 20px; top: 116px;
    font-size: 26px; line-height: 31px; color: var(--grey);
  }
  .process-label {
    position: absolute; left: 27px; top: 262px;
    font-size: 49px; font-weight: 700; color: var(--green-1);
  }
  .package-shapes { position: absolute; left: 0; top: 0; }

  .package-name {
    position: absolute; font-family: "Bebas Neue", "Arial Narrow", sans-serif;
    font-size: 62px; line-height: 1; color: var(--white); text-align: center;
  }
  .package-price {
    position: absolute; font-size: 30px; font-weight: 700; line-height: 35px;
    color: var(--white); text-align: center;
  }
  .sorglos-head {
    position: absolute; left: 657px; top: 165px; width: 270px;
    font-size: 31px; font-weight: 700; line-height: 35px; color: var(--white);
  }

  .service-list { position: absolute; list-style: none; color: var(--white); font-size: 18px; line-height: 21px; }
  .service-list li { position: relative; padding-left: 18px; margin-bottom: 8px; }
  .service-list li::before {
    content: ""; position: absolute; left: 3px; top: 5px;
    width: 4px; height: 7px;
    border-right: 1.6px solid var(--white); border-bottom: 1.6px solid var(--white);
    transform: rotate(45deg);
  }
  .list-basis { left: 40px; top: 564px; width: 272px; }
  .list-medium { left: 348px; top: 497px; width: 275px; }
  .list-sorglos { left: 640px; top: 377px; width: 290px; }

  .brand-name {
    position: absolute; left: 100px; top: 1252px; width: 390px; text-align: center;
    font-size: 68px; font-weight: 500; color: var(--green-1); letter-spacing: 0.5px;
  }
</style>
</head>
<body>
<main class="flyer">
  <div class="top-band"><span></span><span></span></div>

  <h1 class="flyer-title">Individuelle Vermarktungspakete</h1>
  <p class="flyer-note">Unterlagen müssen gestellt werden, ansonsten<br>werden Sie 1:1 verrechnet: GB-Auszug,GVZ,<br>Nebenkostenabrechnung, STWEG-Protokolle der<br>letzten 3 Jahren, …</p>
  <h2 class="process-label">Verkaufsablauf:</h2>

  <svg class="package-shapes" width="959" height="1357" viewBox="0 0 959 1357" aria-hidden="true">
    <polygon points="19,437 148,338 323,397 323,1202 19,1300" fill="var(--red)"/>
    <polygon points="323,397 485,250 629,327 629,1342 323,1202" fill="var(--blue)"/>
    <rect x="629" y="151" width="305" height="1191" fill="var(--green-2)"/>
  </svg>

  <div class="package-name" style="left:72px;top:400px;width:200px;">Basis</div>
  <div class="package-price" style="left:22px;top:468px;width:300px;">-Paket 8'500.<br>- CHF exkl. MWST</div>
  <ul class="service-list list-basis">
    <li>Begehung Verkaufsobjekt</li>
    <li>Hedonische Schätzung intern &amp; Bank</li>
    <li>Marketing &amp; Vertriebskonzept</li>
    <li>Unterlagen einfordern- STWEG</li>
    <li>Protokolle, GB Auszug u.s.w wenn nötig</li>
    <li>Fotografieren &amp; Ausmessen der Immobilie</li>
    <li>Grundriss zeichnen</li>
    <li>Dokumentation erstellen</li>
    <li>Unsere Interessenten anschreiben</li>
    <li>Immobilie Online aufbereiten &amp; Aufschalten</li>
    <li>Anfragen beantworten- telefonisch &amp; elektronisch</li>
    <li>Interessenten &amp; Kaufangebote prüfen</li>
    <li>Käufer zusage- andere noch vertrösten</li>
    <li>Erstellung erster Kaufvertragsentwurf</li>
  </ul>

  <div class="package-name" style="left:375px;top:340px;width:200px;">Medium</div>
  <div class="package-price" style="left:325px;top:395px;width:300px;">-Paket 10’900<br>CHF exkl. MWST</div>
  <ul class="service-list list-medium">
    <li>Begehung Verkaufsobjekt</li>
    <li>Hedonische Schätzung intern &amp; Bank</li>
    <li>Marketing &amp; Vertriebskonzept</li>
    <li>Unterlagen einfordern- STWEG</li>
    <li>Protokolle, GB Auszug u.s.w wenn nötig</li>
    <li>Fotografieren &amp; Ausmessen der Immobilie</li>
    <li>Grundriss zeichnen</li>
    <li>Dokumentation erstellen</li>
    <li>Unsere Interessenten anschreiben</li>
    <li>Immobilie Online aufbereiten &amp; Aufschalten</li>
    <li>Anfragen beantworten- telefonisch &amp; elektronisch</li>
    <li>Interessenten &amp; Kaufangebote prüfen</li>
    <li>Evt. Bieterverfahren modern oder altmodisch</li>
    <li>Käufer zusage- andere noch vertrösten</li>
    <li>Erstellung erster Kaufvertragsentwurf</li>
    <li>Begleitung aufs Notariat</li>
  </ul>

  <h3 class="sorglos-head">Sorglos: 2% vom Verkaufspreis inkl. MWST (von Grundstückge-winnsteuer abziehbar)</h3>
  <ul class="service-list list-sorglos">
    <li>Begehung Verkaufsobjekt</li>
    <li>Hedonische Schätzung intern &amp; Bank</li>
    <li>Marketing &amp; Vertriebskonzept</li>
    <li>Unterlagen einfordern- STWEG</li>
    <li>Protokolle, GB Auszug u.s.w wenn nötig</li>
    <li>Fotografieren &amp; Ausmessen der Immobilie</li>
    <li>Grundriss zeichnen</li>
    <li>Dokumentation erstellen</li>
    <li>Unsere Interessenten anschreiben</li>
    <li>Immobilie Online aufbereiten &amp; Aufschalten</li>
    <li>Anfragen beantworten- telefonisch &amp; elektronisch</li>
    <li>Besichtigungen koordinieren</li>
    <li>Besichtigungen Durchführen</li>
    <li>Interessenten &amp; Kaufangebote prüfen</li>
    <li>Evt. Bieterverfahren modern oder altmodisch</li>
    <li>Käufer zusage- andere noch ver-trösten</li>
    <li>Sicherheitsnachweis (SINA)- organisieren</li>
    <li>Erstellung erster Kaufvertragsentwurf</li>
    <li>Berechnung provisorische Grund</li>
    <li>Beurkundungstermin vereinbaren</li>
    <li>Begleitung aufs Notariat</li>
    <li>Eigentumsübertragung verein-baren</li>
    <li>Helfen bei der Steuererklärung für die definitive Grundstückge-winnsteuer</li>
  </ul>

  <div class="brand-name">Brivotelo</div>
</main>
</body>
</html>
```